TalkHarbor - Language Coaching Services

Sleek, innovative, trendy design for Language Coaching business.

TalkHarbor is a new UK based company that provides Language Coaching services. We offer highly personalized on-line and face to face language courses. We also impart learning techniques workshops based on the latest neuroscience research for second-language acquisition.

Target Market(s)

See attached info

Industry/Entity Type

Consulting

Contact Information for Business Card

TalkHarbor
DaniaKV@talkharbor.co.uk
TalkHarbor.co.uk
London, UK

Font styles to use
Sans Serif

```html
<!DOCTYPE html>
<html lang="en">
<head>
<meta charset="utf-8">
<title>TalkHarbor Business Card</title>
<link rel="stylesheet" href="https://fonts.googleapis.com/css2?family=Roboto:wght@300;400;700&display=swap">
<style>
  :root {
    --page-bg: #e9eaeb;
    --card-white: #ffffff;
    --brand-blue: #1f8fc4;
    --brand-deep: #0b6a9c;
    --brand-light: #1db4e8;
    --text-grey: #5a5a5a;
    --muted-grey: #9a9a9a;
    --rule-grey: #d8d8d8;
    --strip-grey: #d2d3d4;
  }
  * { margin: 0; padding: 0; box-sizing: border-box; }
  html, body {
    width: 1125px; height: 1200px; overflow: hidden;
    background: var(--page-bg);
    font-family: "Roboto", Arial, sans-serif;
  }
  .canvas { position: relative; width: 1125px; height: 1200px; }
  .card {
    position: absolute; left: 150px; width: 825px; height: 470px;
    border-radius: 22px; overflow: hidden;
  }
  .card-front { top: 98px; background: var(--card-white); }
  .card-back {
    top: 630px;
    background: radial-gradient(ellipse 60% 70% at 50% 48%, var(--brand-light) 0%, #1597cd 45%, var(--brand-deep) 100%);
  }
  .brand-block { position: absolute; left: 100px; top: 95px; width: 290px; text-align: center; }
  .brand-mark {
    width: 116px; height: 116px; margin: 0 auto 20px;
    border: 9px solid var(--brand-blue); border-radius: 50%;
  }
  .brand-name {
    font-weight: 400; font-size: 40px; letter-spacing: 1px;
    color: var(--brand-blue); line-height: 1;
  }
  .divider {
    position: absolute; left: 443px; top: 152px; width: 1px; height: 171px;
    background: var(--rule-grey);
  }
  .contact-block { position: absolute; left: 474px; top: 150px; }
  .person-name { font-size: 31px; color: var(--brand-blue); line-height: 1; letter-spacing: 0.5px; }
  .person-name strong { font-weight: 700; }
  .person-name span { font-weight: 300; }
  .person-role { font-size: 20px; font-weight: 700; color: var(--muted-grey); margin-top: 6px; }
  .contact-list { list-style: none; margin-top: 22px; }
  .contact-list li {
    display: flex; align-items: center; gap: 13px;
    font-size: 19.5px; color: var(--text-grey); height: 27px;
  }
  .contact-list svg { width: 16px; height: 16px; flex: none; }
  .accent-strip {
    position: absolute; left: 0; bottom: 0; width: 100%; height: 12px;
    background: linear-gradient(100deg, #1a7fb0 0%, var(--brand-light) 40%, #127fb5 75%, var(--brand-deep) 80.5%, #fff 80.5%, #fff 81%, var(--strip-grey) 81%);
  }
  .back-mark {
    position: absolute; left: 284px; top: 96px; width: 258px; height: 258px;
    border: 13px solid #fff; border-radius: 50%;
  }
  .back-name {
    position: absolute; left: 0; width: 100%; top: 208px; text-align: center;
    font-size: 34px; font-weight: 400; color: #fff; letter-spacing: 1px;
  }
  .back-url {
    position: absolute; left: 0; width: 100%; top: 400px; text-align: center;
    font-size: 19px; font-weight: 300; letter-spacing: 6px;
    color: rgba(255,255,255,0.75);
  }
</style>
</head>
<body>
<main class="canvas">
  <section class="card card-front">
    <div class="brand-block">
      <div class="brand-mark"></div>
      <div class="brand-name">TALKHARBOR</div>
    </div>
    <div class="divider"></div>
    <div class="contact-block">
      <h1 class="person-name"><strong>DANIA</strong> <span>KOVAC</span></h1>
      <p class="person-role">CEO/Founder</p>
      <ul class="contact-list">
        <li>
          <svg viewBox="0 0 16 16"><rect x="3.5" y="0.5" width="9" height="15" rx="1.5" fill="none" stroke="#1f8fc4" stroke-width="1.6"/><rect x="5" y="2.5" width="6" height="9" fill="#1f8fc4"/></svg>
          020 7946 0381
        </li>
        <li>
          <svg viewBox="0 0 16 16"><rect x="0.5" y="3" width="15" height="10" fill="#1f8fc4"/><path d="M0.5 3 L8 9 L15.5 3" fill="none" stroke="#fff" stroke-width="1.4"/></svg>
          info@talkharbor.co.uk
        </li>
        <li>
          <svg viewBox="0 0 16 16"><circle cx="8" cy="8" r="7.5" fill="#1f8fc4"/><path d="M4 5 Q6 4 7 6 T6 10 M10 3 Q12 6 11 10" fill="none" stroke="#fff" stroke-width="1.3"/></svg>
          www.talkharbor.co.uk
        </li>
      </ul>
    </div>
    <div class="accent-strip"></div>
  </section>

  <section class="card card-back">
    <div class="back-mark"></div>
    <div class="back-name" style="top:380px;display:none"></div>
    <p class="back-url">www.talkharbor.co.uk</p>
  </section>
</main>
</body>
</html>
```